Business card design needed

I run a Beautician studio (for 7 years now)
I offer
- Velmo Body Sugaring
- Ruby Glaze
- Nails
- Facials
- Manicure
- Foot Treatment
It might not be necessary to list all those treatments?
Maybe the link to the Website is sufficient?
I leave that up to you ...
(more info on www.FernAndDewByLenka.com.au)
Velmo BodySugaring is our biggest success, It replaces waxing.
I would like to incorporate the logo into the Business Card.
We had many complaints regarding our old Business Cards as the Phone Number was to small.
On the backside, we would like a "your next Appointment" section.
Looking forward to you Design, cheers ... Lenka
Industry/Entity Type
Business
Contact Information for Business Card
Fern by Dew by Lenka
14 Korrin Sqr 3942 Calloway
www.FernAndDewByLenka.com.au
03 9481 2267

```html
<!DOCTYPE html>
<html lang="en">
<head>
<meta charset="utf-8">
<title>Fern &amp; Dew by Lenka – Business Cards</title>
<link rel="stylesheet" href="https://fonts.googleapis.com/css2?family=Didact+Gothic&family=Open+Sans:ital,wght@0,400;0,600;1,600;1,700&family=Tinos&display=swap">
<style>
  :root {
    --backdrop: #e8e4df;
    --card: #ffffff;
    --ink: #3b3b3b;
    --ink-soft: #555555;
    --rule: #9a9a9a;
    --band: #414141;
    --band-light: #b9b9b9;
    --brand: #4a4a4a;
    --mark: #e9a23b;
    --ghost: rgba(120, 120, 120, 0.10);
  }
  * { box-sizing: border-box; margin: 0; padding: 0; }
  html, body { width: 1200px; height: 788px; overflow: hidden; }
  body {
    position: relative;
    background: var(--backdrop);
    font-family: "Open Sans", sans-serif;
    color: var(--ink);
  }
  .view-label {
    position: absolute;
    font-size: 21px;
    color: #111;
    transform: translateX(-50%);
  }
  .card {
    position: absolute;
    width: 525px;
    height: 301px;
    background: var(--card);
    border-radius: 18px;
    overflow: hidden;
    box-shadow: 0 3px 8px rgba(0,0,0,0.25);
  }
  .card > * { position: absolute; }
  .studio-name {
    font-family: "Didact Gothic", sans-serif;
    font-weight: 400;
    letter-spacing: 1.5px;
    color: var(--ink);
    white-space: nowrap;
    transform: translateX(-50%);
  }
  .brand-name {
    font-family: "Open Sans", sans-serif;
    font-weight: 600;
    color: var(--brand);
    letter-spacing: 4px;
    display: flex;
    align-items: center;
    gap: 8px;
    white-space: nowrap;
  }
  .brand-dot {
    width: 14px; height: 14px; border-radius: 50%;
    background: var(--mark);
  }

  /* Front */
  .card--front { left: 326px; top: 74px; }
  .card--front .studio-name { left: 50%; top: 31px; font-size: 36px; }
  .card--front .brand-name { left: 50%; transform: translateX(-50%); top: 130px; font-size: 24px; }
  .contact { left: 0; width: 100%; text-align: center; font-size: 16.5px; color: var(--ink); }
  .contact--phone { top: 190px; }
  .contact--web { top: 216px; }
  .contact svg { vertical-align: -2px; margin-right: 3px; }
  .swoosh { left: 0; bottom: 0; width: 525px; height: 60px; }
  .address { right: 86px; bottom: 10px; color: #fff; font-size: 16px; }

  /* Back 1 */
  .card--offer { left: 54px; top: 443px; }
  .card--offer .studio-name { left: 50%; top: 12px; font-size: 26px; }
  .title-rule { left: 0; top: 51px; width: 100%; height: 1px; background: var(--ink-soft); }
  .ghost-brand {
    left: 130px; top: 150px;
    font-family: "Open Sans", sans-serif; font-weight: 600;
    font-size: 58px; letter-spacing: 10px; color: var(--ghost);
  }
  .section-head { font-style: italic; font-weight: 700; font-size: 17px; color: var(--ink); }
  .offer-head { left: 29px; top: 70px; }
  .offer-list { left: 29px; top: 97px; list-style: none; font-family: "Tinos", serif; font-size: 15px; color: var(--ink-soft); line-height: 20px; }
  .offer-list li::before { content: ""; display: inline-block; width: 5px; height: 5px; background: var(--ink-soft); margin-right: 7px; vertical-align: 3px; }
  .col-divider { left: 206px; top: 72px; width: 2px; height: 140px; background: linear-gradient(#ddd, #888 50%, #ddd); }
  .appt-head { left: 244px; top: 70px; }
  .field { left: 244px; font-size: 16px; color: var(--ink-soft); display: flex; align-items: flex-end; white-space: nowrap; }
  .field .blank { display: inline-block; border-bottom: 1px solid var(--ink-soft); height: 18px; }
  .field--name { top: 110px; }
  .field--date { top: 150px; }
  .field--time { top: 190px; }
  .hours-head { left: 0; width: 100%; text-align: center; top: 238px; font-size: 14px; font-style: italic; font-weight: 700; color: var(--ink); }
  .hours-line { left: 60px; top: 261px; font-size: 12.5px; color: var(--ink); white-space: nowrap; }
  .hours-line span + span { margin-left: 54px; }

  /* Back 2 */
  .card--appointment { left: 621px; top: 443px; }
  .hours-title { left: 33px; top: 27px; font-size: 20px; font-style: italic; font-weight: 600; letter-spacing: 1.3px; color: var(--ink); }
  .hours-rows { left: 30px; top: 61px; font-size: 17px; line-height: 24px; color: var(--ink); }
  .card--appointment .brand-name { left: 382px; top: 68px; font-size: 20px; }
  .card-rule { left: 29px; top: 117px; width: 467px; height: 1px; background: var(--rule); }
  .appt-line { left: 46px; top: 143px; font-size: 18px; color: var(--ink); display: flex; align-items: flex-end; white-space: nowrap; }
  .appt-line .blank { display: inline-block; border-bottom: 1px solid var(--ink); height: 20px; }
  .date-row { left: 35px; top: 194px; }
  .day-row { left: 59px; top: 248px; display: flex; font-size: 17px; color: var(--ink); }
  .day { display: flex; align-items: center; gap: 11px; margin-right: 15px; }
  .box { width: 22px; height: 22px; border: 1px solid #333; }
</style>
</head>
<body>

<span class="view-label" style="left:592px;top:33px;">Front</span>
<span class="view-label" style="left:324px;top:402px;">Back - 1</span>
<span class="view-label" style="left:896px;top:402px;">Back - 2</span>

<section class="card card--front">
  <h1 class="studio-name">FERN&amp;DEW BY LENKA</h1>
  <div class="brand-name"><span class="brand-dot"></span>VELMO</div>
  <p class="contact contact--phone">
    <svg width="13" height="13" viewBox="0 0 14 14" aria-hidden="true"><circle cx="7" cy="7" r="6" fill="none" stroke="#3b3b3b" stroke-width="1.2"/><path d="M4.5 4 L6 5.8 L5.3 6.6 Q6.3 8.3 7.6 8.9 L8.4 8.1 L10 9.6 L9.2 10.5 Q6.3 10 4 6 Z" fill="#3b3b3b"/></svg>03 9481 2267
  </p>
  <p class="contact contact--web">
    <svg width="11" height="11" viewBox="0 0 12 12" aria-hidden="true"><circle cx="6" cy="6" r="5.5" fill="#3b3b3b"/></svg>www.FernAndDewByLenka.com.au
  </p>
  <svg class="swoosh" viewBox="0 0 525 60" aria-hidden="true">
    <path d="M0 60 L0 22 C120 10 250 4 400 8 C240 10 110 22 0 40 Z" fill="var(--band-light)"/>
    <path d="M0 60 L0 50 C150 24 330 12 525 16 L525 60 Z" fill="var(--band)"/>
  </svg>
  <p class="address">14 Korrin Sqr, 3942 Calloway</p>
</section>

<section class="card card--offer">
  <div class="ghost-brand" aria-hidden="true">VELMO</div>
  <h2 class="studio-name">FERN&amp;DEW BY LENKA</h2>
  <div class="title-rule"></div>
  <h3 class="section-head offer-head">I offer</h3>
  <ul class="offer-list">
    <li>Velmo Body Sugaring</li>
    <li>Ruby Glaze</li>
    <li>Nails</li>
    <li>Facials</li>
    <li>Manicure</li>
    <li>Foot Treatment</li>
  </ul>
  <div class="col-divider"></div>
  <h3 class="section-head appt-head">An Appointment</h3>
  <p class="field field--name">Name<span class="blank" style="width:216px"></span></p>
  <p class="field field--date">Date<span class="blank" style="width:226px"></span></p>
  <p class="field field--time">time<span class="blank" style="width:160px"></span>&nbsp;am / pm</p>
  <h4 class="hours-head">Hours of Operation</h4>
  <p class="hours-line"><span>Mon. to Fri.&nbsp; 7.30am - 7.00pm</span><span>Sat. 7.30am - 12.00pm</span></p>
</section>

<section class="card card--appointment">
  <h2 class="hours-title">Hours of Operation</h2>
  <p class="hours-rows">Monday to Friday -&nbsp; 7.30am - 7.00pm<br>Saturday - 7.30am - 12.00pm</p>
  <div class="brand-name"><span class="brand-dot"></span>VELMO</div>
  <div class="card-rule"></div>
  <p class="appt-line"><span class="blank" style="width:260px"></span>&nbsp;has an appointment</p>
  <p class="appt-line date-row">Date :<span class="blank" style="width:46px"></span>&nbsp;/&nbsp;<span class="blank" style="width:46px"></span>&nbsp;/&nbsp;<span class="blank" style="width:56px"></span>&nbsp;&nbsp;@&nbsp;<span class="blank" style="width:46px"></span>&nbsp;:&nbsp;<span class="blank" style="width:56px"></span>am / pm</p>
  <div class="day-row">
    <span class="day"><span class="box"></span>Mon.</span>
    <span class="day"><span class="box"></span>Tue.</span>
    <span class="day"><span class="box"></span>Wed.</span>
    <span class="day"><span class="box"></span>Thu.</span>
    <span class="day"><span class="box"></span>Fri.</span>
  </div>
</section>

</body>
</html>
```